Business Card Update, need to bring life to the card, two sided color

We need a new business card design, are moving and changing addresses and need a new look, we have the logos already attached but need a new style moving forward. Can incorporate the color of the logo (The Green) as well, maybe a solid back? We deal with safety products revolving around static electricity and safety lighting. Would like to keep same font in second logo as well.

Target Market(s)

Electrical Safety, Lighting

Contact Information for Business Card

Dale Fenwick
Vice President
Office: 770-555-4821
Cell: 770-555-3067
dale@tkfenwick.example
www.tkfenwick.example
4700 West Harbor Boulevard
Suite #150
Roswell, GA 30076

Font styles to use
Serif
Sans Serif

Requirements
Must have
• Since 1918
Nice to have
• Could use the 100 Year Logo for back of card, would like the back of card to be the same green as logo.
Should not have
• No black cards please.

```html
<!DOCTYPE html>
<html lang="en">
<head>
<meta charset="utf-8">
<title>T.K. Fenwick Business Card</title>
<link rel="stylesheet" href="https://fonts.googleapis.com/css2?family=Arimo:wght@700&family=PT+Sans:wght@400&display=swap">
<style>
  :root {
    --stage: #a6a39b;
    --stage-edge: #2b2b2b;
    --green: #009a5b;
    --green-deep: #006b3f;
    --green-pale: #d9f3e6;
    --white: #ffffff;
    --paper-soft: #fafafa;
    --ink: #111111;
    --card-edge: #8a8a8a;
  }
  html, body { margin: 0; padding: 0; overflow: hidden; }
  .canvas {
    position: relative;
    width: 1200px; height: 862px;
    box-sizing: border-box;
    background: var(--stage);
    border: 3px solid var(--stage-edge);
    overflow: hidden;
  }
  .card {
    position: absolute;
    border-radius: 20px;
    border: 1px solid var(--card-edge);
    overflow: hidden;
    font-family: "PT Sans", sans-serif;
  }
  .card-front { left: 76px; top: 18px; width: 695px; height: 397px; background: var(--white); }
  .card-back { left: 455px; top: 435px; width: 707px; height: 404px; background: var(--paper-soft); }

  .brand { position: absolute; display: flex; align-items: center; }
  .brand-dot { border-radius: 50%; background: var(--green); flex: none; }
  .brand-name {
    font-family: "Arimo", sans-serif; font-weight: 700; color: var(--green);
    line-height: 1.05; white-space: nowrap;
  }
  .brand-name .line { display: block; }
  .brand-since { font-family: "PT Sans", sans-serif; font-weight: 400; color: var(--green-deep); }

  .card-front .brand { left: 36px; top: 32px; }
  .card-front .brand-dot { width: 108px; height: 108px; margin-right: 24px; }
  .card-front .brand-name .primary { font-size: 33px; }
  .card-front .brand-name .secondary { font-size: 17px; margin-left: 24px; margin-top: 2px; }
  .card-front .brand-since { font-size: 15px; margin-left: 24px; margin-top: 6px; letter-spacing: 1px; }

  .address { position: absolute; left: 34px; top: 210px; margin: 0; font-size: 17px; color: var(--ink); white-space: nowrap; }

  .band-rule { position: absolute; left: 0; right: 0; background: var(--green-deep); }
  .card-front .band-rule { top: 246px; height: 4px; }
  .card-front .band { position: absolute; left: 0; right: 0; top: 252px; bottom: 0; background: var(--green); }
  .notch { position: absolute; left: 100px; top: 250px; width: 0; height: 0;
    border-left: 13px solid transparent; border-right: 13px solid transparent; border-top: 13px solid var(--white); }

  .person { position: absolute; left: 34px; top: 298px; font-family: "Arimo", sans-serif; font-weight: 700; white-space: nowrap; }
  .person-name { color: var(--white); font-size: 25px; line-height: 1.25; }
  .person-title { color: var(--green-pale); font-size: 23px; line-height: 1.25; }

  .contacts { position: absolute; left: 380px; top: 283px; margin: 0; padding: 0; list-style: none; }
  .contacts li { display: flex; align-items: center; height: 33px; color: var(--white); font-size: 18px; white-space: nowrap; }
  .contacts svg { width: 16px; height: 16px; margin-right: 6px; flex: none; }

  .card-back .brand { left: 84px; top: 122px; }
  .card-back .brand-dot { width: 130px; height: 130px; margin-right: 18px; }
  .card-back .brand-name .primary { font-size: 42px; }
  .card-back .brand-name .secondary { font-size: 22px; margin-left: 30px; margin-top: 4px; }
  .card-back .brand-since { font-size: 18px; margin-left: 30px; margin-top: 8px; letter-spacing: 1px; }

  .card-back .band-rule { top: 356px; height: 3px; }
  .card-back .band { position: absolute; left: 0; right: 0; top: 359px; bottom: 0; background: var(--green);
    display: flex; align-items: center; justify-content: center; }
  .band-url { color: var(--white); font-size: 20px; letter-spacing: 6px; }
</style>
</head>
<body>
<main class="canvas">
  <section class="card card-front">
    <div class="brand">
      <span class="brand-dot"></span>
      <span class="brand-name">
        <span class="line primary">T.K. Fenwick</span>
        <span class="line secondary">Manufacturing Company, Inc.</span>
        <span class="line brand-since">Since 1918</span>
      </span>
    </div>
    <p class="address">4700 West Harbor Boulevard, Suite #150, Roswell, GA 30076</p>
    <div class="band-rule"></div>
    <div class="band"></div>
    <div class="notch"></div>
    <div class="person">
      <div class="person-name">Dale Fenwick</div>
      <div class="person-title">Vice President</div>
    </div>
    <ul class="contacts">
      <li>
        <svg viewBox="0 0 16 16"><circle cx="8" cy="8" r="7" fill="none" stroke="#ffffff" stroke-width="1.4"/><path d="M5.3 4.5l1.4-.3.8 2-1 .7c.5 1 1.2 1.7 2.2 2.2l.7-1 2 .8-.3 1.4c-3.2.3-6-2.5-5.8-5.8z" fill="#ffffff"/></svg>
        770-555-4821
      </li>
      <li>
        <svg viewBox="0 0 16 16" fill="none" stroke="#ffffff" stroke-width="1.1"><circle cx="8" cy="8" r="6.5"/><ellipse cx="8" cy="8" rx="3" ry="6.5"/><path d="M1.5 8h13M2.5 5h11M2.5 11h11"/></svg>
        www.tkfenwick.example
      </li>
      <li>
        <svg viewBox="0 0 16 16" fill="none" stroke="#ffffff" stroke-width="1.3"><circle cx="8" cy="8" r="7"/><rect x="4" y="5.5" width="8" height="5.5"/><path d="M4 5.5l4 3 4-3"/></svg>
        dale@tkfenwick.example
      </li>
    </ul>
  </section>

  <section class="card card-back">
    <div class="brand">
      <span class="brand-dot"></span>
      <span class="brand-name">
        <span class="line primary">T.K. Fenwick</span>
        <span class="line secondary">Manufacturing Company, Inc.</span>
        <span class="line brand-since">Since 1918</span>
      </span>
    </div>
    <div class="band-rule"></div>
    <div class="band"><span class="band-url">www.tkfenwick.example</span></div>
  </section>
</main>
</body>
</html>
```